QVR business card

Need a business card for a company that provides instructional design and elearning development services. The website is here: http://quorvane.studio/

I'm attaching a current logo, as well as the old business card design. While I like to keep it clean, the old design is too simplistic for my liking. The only idea I want to reuse from the old design is placing industry jargon on the back of the card, just need a better way to present it. But if you have other ideas for the back--feel free to experiment.

Please use the colors complementary to the color we have on the website. Thank you!

```html
<!DOCTYPE html>
<html lang="en">
<head>
<meta charset="utf-8">
<title>QVR business card</title>
<link rel="stylesheet" href="https://fonts.googleapis.com/css2?family=Open+Sans:wght@400;600;700&display=swap">
<style>
  :root {
    --backdrop: #e4e4e4;
    --paper: #ffffff;
    --teal: #12b3ad;
    --sand: #ddd194;
    --ink: #2f2f2f;
    --logo-sand: #cfc07a;
    --white: #ffffff;
  }
  * { box-sizing: border-box; margin: 0; padding: 0; }
  html, body { width: 1200px; height: 726px; overflow: hidden; }
  body {
    background: var(--backdrop);
    font-family: "Open Sans", Arial, sans-serif;
    position: relative;
  }
  .card {
    position: absolute;
    top: 213px;
    width: 520px;
    height: 300px;
    overflow: hidden;
    box-shadow: 0 4px 14px rgba(0,0,0,.12);
  }
  /* Front */
  .card-front { left: 50px; background: var(--paper); }
  .brand {
    position: absolute;
    top: 38px; left: 0; width: 100%;
    display: flex; justify-content: center; align-items: center; gap: 12px;
  }
  .brand-dot { width: 22px; height: 22px; border-radius: 50%; background: var(--teal); }
  .brand-name {
    font-size: 48px; font-weight: 700; color: var(--logo-sand);
    letter-spacing: 2px; line-height: 1;
  }
  .contact-panel {
    position: absolute;
    left: 292px; top: 112px; width: 228px; height: 112px;
    background: var(--sand);
    padding: 20px 0 0 20px;
    list-style: none;
  }
  .contact-panel li {
    display: flex; align-items: center; gap: 9px;
    font-size: 13px; color: var(--ink); line-height: 22px;
  }
  .contact-panel svg { width: 12px; height: 12px; flex: none; }
  .name-band {
    position: absolute;
    left: 0; top: 160px; width: 292px; height: 100px;
    background: var(--teal);
    padding: 28px 0 0 40px;
  }
  .name-band::before {
    content: ""; position: absolute; top: 0; left: 120px;
    border-left: 12px solid transparent; border-right: 12px solid transparent;
    border-top: 10px solid var(--paper);
  }
  .person-name {
    font-size: 17px; font-weight: 700; color: var(--white);
    letter-spacing: .5px; line-height: 1.2;
  }
  .person-role { font-size: 13px; color: var(--ink); padding-left: 40px; }
  /* Back */
  .card-back {
    left: 630px;
    background: linear-gradient(160deg, var(--teal) 0%, #7cc3a6 45%, var(--sand) 100%);
  }
  .map-area {
    position: absolute; left: 120px; top: 60px; width: 380px; height: 180px;
    background: radial-gradient(ellipse at center, rgba(30,120,110,.22), rgba(30,120,110,0) 70%);
  }
  .back-brand {
    position: absolute; top: 62px; left: 0; width: 100%;
    display: flex; justify-content: center; align-items: center; gap: 10px;
  }
  .back-brand .brand-dot { background: var(--white); width: 18px; height: 18px; }
  .back-brand .brand-name { color: var(--white); font-size: 40px; }
  .services {
    position: absolute; top: 142px; left: 0; width: 100%;
    display: flex; flex-direction: column; align-items: center; gap: 5px;
    list-style: none;
  }
  .services li {
    background: var(--teal); color: var(--white);
    font-size: 15px; line-height: 20px; padding: 0 6px;
  }
  .back-url {
    position: absolute; top: 244px; width: 100%; text-align: center;
    font-size: 12px; color: var(--white);
  }
</style>
</head>
<body>
  <section class="card card-front">
    <div class="brand">
      <span class="brand-dot"></span>
      <span class="brand-name">QVR</span>
    </div>
    <ul class="contact-panel">
      <li>
        <svg viewBox="0 0 12 12"><path fill="var(--teal)" d="M2 1h2l1 3-1.5 1a7 7 0 0 0 3.5 3.5L8 7l3 1v2a1 1 0 0 1-1 1A9 9 0 0 1 1 2a1 1 0 0 1 1-1z"/></svg>
        555-014-2380
      </li>
      <li>
        <svg viewBox="0 0 12 12"><rect x="1" y="2.5" width="10" height="7" rx="1" fill="var(--teal)"/><path d="M1.5 3l4.5 3.5L10.5 3" fill="none" stroke="var(--sand)" stroke-width="1"/></svg>
        dmerrow@quorvane.studio
      </li>
      <li>
        <svg viewBox="0 0 12 12"><circle cx="6" cy="6" r="5" fill="none" stroke="var(--teal)" stroke-width="1.3"/><path d="M1 6h10M6 1c-3 3-3 7 0 10M6 1c3 3 3 7 0 10" fill="none" stroke="var(--teal)" stroke-width="1"/></svg>
        www.quorvane.studio
      </li>
    </ul>
    <div class="name-band">
      <p class="person-name">DANA MERROW</p>
      <p class="person-role">Managing Director</p>
    </div>
  </section>

  <section class="card card-back">
    <div class="map-area" role="img" aria-label="Dotted world map"></div>
    <div class="back-brand">
      <span class="brand-dot"></span>
      <span class="brand-name">QVR</span>
    </div>
    <ul class="services">
      <li>Instructional Design</li>
      <li>Elearning Development | Mobile Learning</li>
      <li>Instructor-LED Training</li>
    </ul>
    <p class="back-url">www.quorvane.studio</p>
  </section>
</body>
</html>
```